Marlow Sail Works President Business Card Carbon fiber catamarans

Hi.. I need a new business card design.. I am the President of a high tech yacht builder. We build Carbon Fiber go fast catamarans... Maybe we use the file I am sharing to you as the back of the card.. We need to look cool and crisp ...

Target Market(s)

Affluent People who will purchase a cool yacht

Industry/Entity Type

Custom Yacht Builder

Contact Information for Business Card

Dean Pellway , President, 731.508.2164 USA

Font styles to use
Serif

Requirements
Must have
• the clean crisp cool feel
Nice to have
• clean and crisp
Should not have
• Bold ugly

```html
<!DOCTYPE html>
<html lang="en">
<head>
<meta charset="utf-8">
<title>Marlow Sail Works – Business Card</title>
<link href="https://fonts.googleapis.com/css2?family=Michroma&family=Nunito+Sans:wght@400&display=swap" rel="stylesheet">
<style>
  :root {
    --stage: #1c1c1c;
    --card-dark: #0b0b0b;
    --card-mid: #1a1a1a;
    --silver: #d9d9d9;
    --silver-soft: #bdbdbd;
    --rule: #3a3a3a;
  }
  html, body {
    margin: 0;
    width: 1200px;
    height: 1015px;
    overflow: hidden;
    background: radial-gradient(ellipse at 50% 45%, #2a2a2a 0%, var(--stage) 55%, #0e0e0e 100%);
  }
  .stage {
    position: relative;
    width: 1200px;
    height: 1015px;
  }
  .card {
    position: absolute;
    left: 290px;
    width: 620px;
    height: 354px;
    border-radius: 3px;
    overflow: hidden;
    box-shadow: 0 18px 40px rgba(0,0,0,0.6);
  }
  .card--front { top: 120px; }
  .card--back  { top: 540px; }
  .card__texture {
    position: absolute;
    inset: 0;
    background: linear-gradient(135deg, var(--card-mid) 0%, var(--card-dark) 60%, #050505 100%);
  }
  .wordmark {
    position: absolute;
    display: flex;
    align-items: center;
    gap: 16px;
    font-family: "Michroma", sans-serif;
    color: var(--silver);
    letter-spacing: 0.16em;
    line-height: 1.25;
    white-space: nowrap;
  }
  .wordmark__name { display: flex; flex-direction: column; }
  .wordmark__dot {
    width: 34px;
    height: 34px;
    border-radius: 50%;
    background: var(--silver);
    flex: none;
  }
  .card--front .wordmark {
    left: 50%;
    top: 50%;
    transform: translate(-50%, -50%);
    font-size: 28px;
  }
  .card--back .wordmark {
    left: 0;
    width: 330px;
    top: 50%;
    transform: translateY(-50%);
    justify-content: center;
    font-size: 16px;
    gap: 12px;
  }
  .card--back .wordmark__dot { width: 24px; height: 24px; }
  .divider {
    position: absolute;
    left: 330px;
    top: 0;
    bottom: 0;
    width: 1px;
    background: var(--rule);
  }
  .contact {
    position: absolute;
    left: 356px;
    top: 62px;
    font-family: "Nunito Sans", sans-serif;
    color: var(--silver);
  }
  .contact__name {
    margin: 0;
    font-family: "Michroma", sans-serif;
    font-size: 15px;
    font-weight: 400;
    letter-spacing: 0.16em;
    text-transform: uppercase;
  }
  .contact__title {
    margin: 4px 0 18px;
    font-size: 14px;
    color: var(--silver-soft);
  }
  .contact__list {
    list-style: none;
    margin: 0;
    padding: 0;
    font-size: 14px;
  }
  .contact__list li {
    display: flex;
    align-items: center;
    gap: 9px;
    margin-bottom: 6px;
  }
  .contact__list li.contact__address { margin-top: 18px; }
  .icon { width: 13px; height: 13px; flex: none; }
</style>
</head>
<body>
<main class="stage">
  <section class="card card--front" aria-label="Card front">
    <div class="card__texture" role="img" aria-label="Dark carbon fibre weave texture"></div>
    <div class="wordmark"><span class="wordmark__dot"></span><span class="wordmark__name"><span>MARLOW</span><span>SAIL WORKS</span></span></div>
  </section>

  <section class="card card--back" aria-label="Card back">
    <div class="card__texture" role="img" aria-label="Dark carbon fibre weave texture"></div>
    <div class="wordmark"><span class="wordmark__dot"></span><span class="wordmark__name"><span>MARLOW</span><span>SAIL WORKS</span></span></div>
    <div class="divider"></div>
    <div class="contact">
      <h1 class="contact__name">Dean Pellway</h1>
      <p class="contact__title">President</p>
      <ul class="contact__list">
        <li>
          <svg class="icon" viewBox="0 0 16 16" aria-hidden="true"><path fill="#d9d9d9" d="M3.5 1.5l2.5 0 1 3.5-1.7 1.2a9 9 0 0 0 4.5 4.5L11 9l3.5 1v2.5c0 1-1 2-2 2A11 11 0 0 1 1.5 3.5c0-1 1-2 2-2z"/></svg>
          731.508.2164
        </li>
        <li>
          <svg class="icon" viewBox="0 0 16 16" aria-hidden="true"><rect x="1" y="3" width="14" height="10" fill="#d9d9d9"/><path d="M1 3l7 6 7-6" fill="none" stroke="#111" stroke-width="1.3"/></svg>
          info@marlowsail.com
        </li>
        <li>
          <svg class="icon" viewBox="0 0 16 16" aria-hidden="true"><g fill="none" stroke="#d9d9d9" stroke-width="1.2"><circle cx="8" cy="8" r="6.5"/><ellipse cx="8" cy="8" rx="3" ry="6.5"/><path d="M1.5 8h13M2.5 4.8h11M2.5 11.2h11"/></g></svg>
          www.marlowsailworks.com
        </li>
        <li class="contact__address">
          <svg class="icon" viewBox="0 0 16 16" aria-hidden="true"><path fill="#d9d9d9" d="M8 1a5 5 0 0 1 5 5c0 3.5-5 9-5 9S3 9.5 3 6a5 5 0 0 1 5-5z"/><circle cx="8" cy="6" r="1.8" fill="#111"/></svg>
          North Carolina 28512, USA
        </li>
      </ul>
    </div>
  </section>
</main>
</body>
</html>
```